Brightfen Business Card Redesign & Logo Update

We need to update our business cards to something more modern and fresh. Brightfen can provide the current color schemes and old design examples, but welcome creativity in helping us with this redesign. PLEASE NOTE that we no longer utilize the "tree" and/or "leaf" imagery in our branding. If able would apprecaite an update on the quality of our "words only" logo in Ai. / PNG formats too.

Target Market(s)

Investors, landowners, corporate partners, contractors

Industry/Entity Type

Environmental Restoration & Conservation

Contact Information for Business Card

Logo, persons name, title, mailing address, phone and email, website url

Font styles to use
Other font styles liked:
• Merriweather

Requirements
Nice to have
• Logo, persons name, title, mailing address, phone and email, website url, but open to ideams
Should not have
• No all back backgrounds

```html
<!DOCTYPE html>
<html lang="en">
<head>
<meta charset="utf-8">
<title>Brightfen Business Card</title>
<link href="https://fonts.googleapis.com/css2?family=Bebas+Neue&family=Oswald:wght@600&family=Merriweather:wght@400;700&display=swap" rel="stylesheet">
<style>
  :root {
    --backdrop: #a3a3a3;
    --card: #ffffff;
    --green: #177c3c;
    --orange: #ef7f22;
    --ink: #1c1c1c;
  }
  * { box-sizing: border-box; margin: 0; padding: 0; }
  html, body { width: 1146px; height: 1200px; overflow: hidden; }
  body { background: var(--backdrop); position: relative; font-family: "Merriweather", Georgia, serif; color: var(--ink); }

  .card { position: absolute; left: 176px; width: 797px; background: var(--card); }
  .card--front { top: 113px; height: 455px; }
  .card--back { top: 595px; height: 469px; }

  .wordmark { font-family: "Bebas Neue", "Oswald", sans-serif; color: var(--green); line-height: 1; letter-spacing: 1px; }
  .tagline { font-family: "Oswald", sans-serif; font-weight: 600; color: var(--ink); text-transform: uppercase; line-height: 1; letter-spacing: -0.3px; }

  .front-lockup { position: absolute; left: 0; right: 0; top: 262px; text-align: center; }
  .front-lockup .wordmark { font-size: 112px; }
  .front-lockup .tagline { font-size: 22px; margin-top: 4px; }

  .back-lockup { position: absolute; right: 39px; top: 58px; text-align: right; }
  .back-lockup .wordmark { font-size: 100px; }
  .back-lockup .tagline { font-size: 20px; margin-top: 2px; text-align: center; }

  .person { position: absolute; left: 40px; top: 215px; }
  .person__name { font-size: 26px; font-weight: 700; text-transform: uppercase; letter-spacing: 0.3px; }
  .person__first { color: var(--orange); }
  .person__last { color: var(--green); }
  .person__title { font-size: 19px; margin-top: 6px; }
  .rule { position: absolute; left: 158px; width: 605px; top: 272px; height: 2px; background: var(--orange); }

  .contacts { position: absolute; left: 40px; top: 308px; list-style: none; font-size: 20px; }
  .contacts li { display: flex; align-items: center; height: 29px; }
  .contacts svg { width: 16px; height: 16px; margin-right: 8px; fill: var(--orange); }

  .address { position: absolute; right: 34px; top: 338px; text-align: right; font-size: 20px; line-height: 29px; }

  .bands { position: absolute; left: 0; bottom: 0; width: 797px; height: 56px; }
</style>
</head>
<body>
  <section class="card card--front">
    <div class="front-lockup">
      <div class="wordmark">Brightfen</div>
      <div class="tagline">Environmental Credit Company</div>
    </div>
  </section>

  <section class="card card--back">
    <div class="back-lockup">
      <div class="wordmark">Brightfen</div>
      <div class="tagline">Environmental Credit Company</div>
    </div>

    <div class="person">
      <div class="person__name"><span class="person__first">Nolan</span> <span class="person__last">Perry</span></div>
      <div class="person__title">Founder</div>
    </div>
    <div class="rule"></div>

    <ul class="contacts">
      <li><svg viewBox="0 0 16 16"><path d="M3 2h3l1 3-2 1.5a9 9 0 0 0 4.5 4.5L11 9l3 1v3a1 1 0 0 1-1 1A12 12 0 0 1 2 3a1 1 0 0 1 1-1z"/></svg>(555) 014-2280</li>
      <li><svg viewBox="0 0 16 16"><path d="M1 4h14v9H1z M1 4l7 5 7-5" stroke="#fff" stroke-width="1.2"/></svg>contact@brightfen.co</li>
      <li><svg viewBox="0 0 16 16"><circle cx="8" cy="8" r="7"/><path d="M1 8h14M8 1c-3 4-3 10 0 14M8 1c3 4 3 10 0 14" stroke="#fff" stroke-width="1" fill="none"/></svg>www.brightfen.co</li>
    </ul>

    <div class="address">
      <div>Your Company Address</div>
      <div>Fen Road 48, PO 2210</div>
    </div>

    <svg class="bands" viewBox="0 0 797 56" aria-hidden="true">
      <polygon points="0,0 344,0 385,56 0,56" fill="var(--green)"/>
      <polygon points="352,11 797,11 797,20 359,20" fill="var(--green)"/>
      <polygon points="372,29 797,29 797,56 392,56" fill="var(--orange)"/>
    </svg>
  </section>
</body>
</html>
```